Tall Fern Roofing Business Card

Need a business card with the logo that was designed here

Contact Information for Business Card

Name, Title, Phone, Email, Website, Company name

```html
<!DOCTYPE html>
<html lang="en">
<head>
<meta charset="utf-8">
<title>Tall Fern Roofing Business Card</title>
<link href="https://fonts.googleapis.com/css2?family=Arimo:wght@400;600;700&display=swap" rel="stylesheet">
<style>
  :root {
    --brand-blue: #1f78c1;
    --band-grey: #939598;
    --paper: #ffffff;
    --backdrop: #2b2b2b;
  }
  * { box-sizing: border-box; margin: 0; padding: 0; }
  html, body { width: 1200px; height: 1015px; overflow: hidden; }
  body {
    background: var(--backdrop);
    font-family: "Arimo", Arial, sans-serif;
    display: flex;
    flex-direction: column;
    align-items: center;
    justify-content: center;
    gap: 30px;
  }
  .card {
    position: relative;
    width: 820px;
    height: 468px;
    overflow: hidden;
  }
  .grey-band {
    position: absolute;
    left: 0; right: 0;
    top: 330px;
    height: 46px;
    background: var(--band-grey);
  }
  .website {
    position: absolute;
    right: 70px;
    top: 330px;
    height: 46px;
    line-height: 46px;
    color: var(--paper);
    font-size: 21px;
    letter-spacing: 1.5px;
  }

  /* Front */
  .card-front { background: var(--brand-blue); }
  .brand {
    position: absolute;
    display: flex;
    align-items: center;
    gap: 14px;
    font-weight: 700;
    font-size: 44px;
    white-space: nowrap;
  }
  .brand-square { width: 22px; height: 22px; flex: none; }
  .card-front .brand {
    left: 0; right: 0;
    top: 150px;
    justify-content: center;
    color: var(--paper);
  }
  .card-front .brand-square { background: var(--paper); }

  /* Back */
  .card-back { background: var(--paper); }
  .info-panel {
    position: absolute;
    top: 0; right: 0; bottom: 0;
    width: 385px;
    background: var(--brand-blue);
  }
  .card-back .brand {
    left: 40px;
    top: 170px;
    font-size: 36px;
    color: var(--brand-blue);
  }
  .card-back .brand-square { background: var(--brand-blue); width: 18px; height: 18px; }
  .contact {
    position: absolute;
    left: 470px;
    top: 100px;
    color: var(--paper);
  }
  .contact-name {
    font-size: 25px;
    font-weight: 700;
    letter-spacing: 0.5px;
  }
  .contact-title {
    font-size: 20px;
    margin-top: 2px;
  }
  .contact-list {
    list-style: none;
    margin-top: 22px;
    font-size: 20px;
  }
  .contact-list li {
    display: flex;
    align-items: center;
    gap: 10px;
    margin-bottom: 6px;
  }
  .contact-list svg { width: 18px; height: 18px; flex: none; }
</style>
</head>
<body>

  <section class="card card-front">
    <div class="brand">
      <span class="brand-square"></span>
      <span class="brand-name">Tall Fern Roofing</span>
    </div>
    <div class="grey-band"></div>
    <div class="website">www.tallfernroofing.com</div>
  </section>

  <section class="card card-back">
    <div class="info-panel"></div>
    <div class="brand">
      <span class="brand-square"></span>
      <span class="brand-name">Tall Fern Roofing</span>
    </div>
    <div class="contact">
      <div class="contact-name">MARCUS HALE</div>
      <div class="contact-title">Managing Director</div>
      <ul class="contact-list">
        <li>
          <svg viewBox="0 0 24 24" aria-hidden="true"><path fill="none" stroke="#fff" stroke-width="2.2" stroke-linecap="round" stroke-linejoin="round" d="M6.5 3.5l3 .5 1.2 4-2 1.5a11 11 0 0 0 5.8 5.8l1.5-2 4 1.2.5 3c-.2 1.5-1.5 2.5-3 2.5C10 20 4 14 4 6.5c0-1.5 1-2.8 2.5-3z"/></svg>
          <span>044-555 018 274</span>
        </li>
        <li>
          <svg viewBox="0 0 24 24" aria-hidden="true"><rect x="2.5" y="5" width="19" height="14" fill="none" stroke="#fff" stroke-width="2"/><path d="M2.5 5l9.5 8 9.5-8" fill="none" stroke="#fff" stroke-width="2"/></svg>
          <span>info@tallfernroofing.com</span>
        </li>
      </ul>
    </div>
    <div class="grey-band"></div>
    <div class="website">www.tallfernroofing.com</div>
  </section>

</body>
</html>
```